Brookmere Osteopathy flyer

I want a clean clear DL flyer (but also want an A4 poster) promoting a new Osteopathic business in a semi rural area in Tasmania (Australia).
It can have pictures like the examples attached to show people what Osteopathy is (its like Chiropractic and physiotherapy).
I am the sole practioner and am male, so any pictures would be best to be a white male if possible.
I've attached some wording, you can use all, or none of it
I don't have a phone number for the business yet
info@brookmereosteopathy.example
www.brookmereosteopathy.example
Target Market(s)
Australians, from tradies, professionals, babies to retired people
Industry/Entity Type
Health
Look and feel

```html
<!DOCTYPE html>
<html lang="en">
<head>
<meta charset="utf-8">
<title>Brookmere Osteopathy – DL Flyer</title>
<link rel="stylesheet" href="https://fonts.googleapis.com/css2?family=Nunito:wght@400;600;700&family=Saira+Condensed:wght@600;700&family=Oswald:wght@500&family=Prata&display=swap">
<style>
  :root{
    --brand-blue:#1787cb;
    --brand-orange:#f6962b;
    --ink:#1e1e1e;
    --paper:#ffffff;
    --backdrop:#ececec;
    --pale-blue:#d4e8f5;
  }
  *{margin:0;padding:0;box-sizing:border-box}
  html,body{width:1191px;height:1200px;overflow:hidden;background:var(--backdrop)}
  body{position:relative;font-family:"Nunito",sans-serif;color:var(--ink)}
  .flyer{position:absolute;width:481px;height:1026px;background:var(--paper);overflow:hidden;box-shadow:0 2px 8px rgba(0,0,0,.15)}
  .flyer--front{left:85px;top:85px}
  .flyer--back{left:619px;top:87px}
  .top-band{position:absolute;left:0;top:0;width:100%;height:46px;background:var(--brand-blue);border-bottom:2px solid var(--brand-orange)}
  .brand-mark{position:absolute;left:19px;top:16px;width:136px;height:136px;border-radius:50%;background:var(--paper);border:3px solid var(--brand-blue);display:flex;align-items:center;justify-content:center;text-align:center;font-weight:700;font-size:15px;line-height:1.15;color:var(--brand-blue)}
  .brand-name{position:absolute;left:167px;top:60px;font-size:27px;font-weight:600;color:var(--brand-blue);letter-spacing:.3px;white-space:nowrap}
  .tagline{position:absolute;left:168px;top:92px;font-family:"Saira Condensed",sans-serif;font-weight:700;font-size:33px;color:var(--brand-orange);white-space:nowrap}
  .intro{position:absolute;left:10px;right:14px;top:163px;font-size:14px;line-height:28.5px;text-align:justify}
  .photo{position:absolute}
  .photo--spine{left:0;top:375px;width:481px;height:282px;background:linear-gradient(135deg,#e8eef3,#cfdde8 60%,#f3f5f7)}
  .photo--infant{left:0;top:657px;width:236px;height:186px;background:linear-gradient(160deg,#9ca6c9,#5b86b3 70%,#8ea4c3)}
  .photo--back-massage{left:247px;top:657px;width:234px;height:186px;background:linear-gradient(160deg,#c9d5dc,#d9b08c 55%,#2f4752)}
  .service-area{position:absolute;left:0;width:100%;top:860px;text-align:center;font-weight:700;font-size:17.5px}
  .offer{position:absolute;left:0;width:100%;top:892px;text-align:center;font-family:"Saira Condensed",sans-serif;font-weight:700;font-size:35px;color:var(--brand-blue);letter-spacing:.3px}
  .spine-decor{position:absolute;left:5px;top:932px;width:470px;height:58px}
  .address{position:absolute;display:flex;align-items:center;gap:14px;white-space:nowrap}
  .flyer--front .address{left:33px;top:980px;font-size:23.5px}
  .photo--clinic{left:0;top:167px;width:485px;height:324px;background:linear-gradient(110deg,#f4f6f7 0%,#e9edef 50%,#d9a35a 78%,#e89a2c 90%,#c9d9e6 100%)}
  .photo-caption{position:absolute;left:23px;top:232px;font-family:"Oswald",sans-serif;font-weight:500;font-size:37px;line-height:44px;color:#111;letter-spacing:-.3px}
  .reasons-title{position:absolute;left:11px;top:508px;font-family:"Saira Condensed",sans-serif;font-weight:700;font-size:29px;color:var(--brand-blue);white-space:nowrap}
  .reasons{position:absolute;left:11px;top:551px;list-style:none}
  .reasons li{display:flex;align-items:center;height:31.7px;font-size:16.5px;letter-spacing:.3px}
  .reasons svg{width:20px;height:14px;margin-right:15px}
  .contact{position:absolute;left:11px;top:886px;display:flex;align-items:flex-start;gap:14px}
  .contact-label{font-size:15px;color:var(--brand-blue);letter-spacing:.3px}
  .contact-phone{font-family:"Prata",serif;font-size:30px;color:var(--brand-blue);line-height:1.1}
  .flyer--back .address{left:11px;top:956px;font-size:23.5px}
  .web-line{position:absolute;left:15px;top:1002px;display:flex;align-items:center;gap:6px;font-size:11px;white-space:nowrap}
  .web-line span{margin-right:8px}
</style>
</head>
<body>

<section class="flyer flyer--front">
  <div class="top-band"></div>
  <div class="brand-mark">Brookmere<br>Osteopathy</div>
  <h1 class="brand-name">Brookmere Osteopathy</h1>
  <p class="tagline">Move Better, Feel Better.</p>
  <p class="intro">Brookmere Osteopathy use a tailored combination of joint mobilisation/manipulation, stretching, movement, trigger point dry needling and targeted massage to reduce pain and restore optimal function. Hands-on treatment is backed up with rehabilitative exercise prescription and advice. So whether you're recovering from injury or managing chronic discomfort, we're here to help you move better &amp; feel your best.</p>
  <div class="photo photo--spine" role="img" aria-label="Practitioner pointing to a model spine and pelvis in a clinic"></div>
  <div class="photo photo--infant" role="img" aria-label="Gentle hands cradling a sleeping newborn's head"></div>
  <div class="photo photo--back-massage" role="img" aria-label="Practitioner treating a woman's lower back"></div>
  <p class="service-area">Serving Semi Rural Area In Tasmania - Australia</p>
  <p class="offer">FREE INTIAL PHYSIO CONSULTATION</p>
  <svg class="spine-decor" viewBox="0 0 470 58" role="img" aria-label="Faint decorative curve">
    <path d="M0 52 C120 40 200 10 470 6 L470 20 C260 24 150 50 0 58 Z" fill="var(--pale-blue)"/>
  </svg>
  <div class="address">
    <svg width="20" height="28" viewBox="0 0 20 28"><path d="M10 0C4.5 0 0 4.4 0 9.9 0 17 10 28 10 28s10-11 10-18.1C20 4.4 15.5 0 10 0z" fill="var(--brand-orange)"/><circle cx="10" cy="10" r="4" fill="#fff"/></svg>
    48 Willow Creek Road, Brookmere
  </div>
</section>

<section class="flyer flyer--back">
  <div class="top-band"></div>
  <div class="brand-mark">Brookmere<br>Osteopathy</div>
  <h1 class="brand-name">Brookmere Osteopathy</h1>
  <p class="tagline">Move Better, Feel Better.</p>
  <div class="photo photo--clinic" role="img" aria-label="Practitioner assisting a smiling patient with a shoulder stretch in a bright treatment room"></div>
  <p class="photo-caption">CHIROPRACTIC<br>AND<br>PHYSIOTHERAPY</p>
  <h2 class="reasons-title">Common Reasons People Visit An Osteopath</h2>
  <ul class="reasons">
    <li><svg viewBox="0 0 20 14"><path d="M1 13 C3 6 8 4 13 4 L13 0 L20 6 L13 12 L13 8 C8 8 4 9 1 13Z" fill="var(--brand-orange)"/></svg>Back / Neck Pain</li>
    <li><svg viewBox="0 0 20 14"><path d="M1 13 C3 6 8 4 13 4 L13 0 L20 6 L13 12 L13 8 C8 8 4 9 1 13Z" fill="var(--brand-orange)"/></svg>Headaches / Migraines</li>
    <li><svg viewBox="0 0 20 14"><path d="M1 13 C3 6 8 4 13 4 L13 0 L20 6 L13 12 L13 8 C8 8 4 9 1 13Z" fill="var(--brand-orange)"/></svg>Joint And Muscle Pain</li>
    <li><svg viewBox="0 0 20 14"><path d="M1 13 C3 6 8 4 13 4 L13 0 L20 6 L13 12 L13 8 C8 8 4 9 1 13Z" fill="var(--brand-orange)"/></svg>Pregnancy-related Discomfort</li>
    <li><svg viewBox="0 0 20 14"><path d="M1 13 C3 6 8 4 13 4 L13 0 L20 6 L13 12 L13 8 C8 8 4 9 1 13Z" fill="var(--brand-orange)"/></svg>Disc Related Issues</li>
    <li><svg viewBox="0 0 20 14"><path d="M1 13 C3 6 8 4 13 4 L13 0 L20 6 L13 12 L13 8 C8 8 4 9 1 13Z" fill="var(--brand-orange)"/></svg>Sciatica</li>
    <li><svg viewBox="0 0 20 14"><path d="M1 13 C3 6 8 4 13 4 L13 0 L20 6 L13 12 L13 8 C8 8 4 9 1 13Z" fill="var(--brand-orange)"/></svg>Plantar Fasciitis</li>
    <li><svg viewBox="0 0 20 14"><path d="M1 13 C3 6 8 4 13 4 L13 0 L20 6 L13 12 L13 8 C8 8 4 9 1 13Z" fill="var(--brand-orange)"/></svg>Tendonitis / Bursitis</li>
    <li><svg viewBox="0 0 20 14"><path d="M1 13 C3 6 8 4 13 4 L13 0 L20 6 L13 12 L13 8 C8 8 4 9 1 13Z" fill="var(--brand-orange)"/></svg>Adhesive Capsulitis (Frozen Shoulder)</li>
    <li><svg viewBox="0 0 20 14"><path d="M1 13 C3 6 8 4 13 4 L13 0 L20 6 L13 12 L13 8 C8 8 4 9 1 13Z" fill="var(--brand-orange)"/></svg>Tennis / Golfers Elbow</li>
  </ul>
  <div class="contact">
    <svg width="38" height="46" viewBox="0 0 38 46"><path d="M8 6 L14 4 L18 15 L13 19 C15 26 19 32 25 36 L30 32 L38 40 L33 45 C18 44 4 26 4 10 Z" fill="none" stroke="var(--brand-blue)" stroke-width="2.2" stroke-linejoin="round"/><path d="M22 4 A14 14 0 0 1 34 17 M22 10 A8 8 0 0 1 28 17" fill="none" stroke="var(--brand-blue)" stroke-width="2.2"/></svg>
    <div>
      <p class="contact-label">Visit Us Today</p>
      <p class="contact-phone">03 5550 0142</p>
    </div>
  </div>
  <div class="address">
    <svg width="20" height="28" viewBox="0 0 20 28"><path d="M10 0C4.5 0 0 4.4 0 9.9 0 17 10 28 10 28s10-11 10-18.1C20 4.4 15.5 0 10 0z" fill="var(--brand-orange)"/><circle cx="10" cy="10" r="4" fill="#fff"/></svg>
    48 Willow Creek Road, Brookmere
  </div>
  <div class="web-line">
    <svg width="11" height="9" viewBox="0 0 11 9"><rect x=".5" y=".5" width="10" height="8" fill="none" stroke="var(--brand-orange)"/><path d="M.5 .5 L5.5 5 L10.5 .5" fill="none" stroke="var(--brand-orange)"/></svg>
    <span>info@brookmereosteopathy.example</span>
    <svg width="11" height="11" viewBox="0 0 11 11"><circle cx="5.5" cy="5.5" r="5" fill="none" stroke="var(--brand-orange)"/><path d="M.5 5.5 H10.5 M5.5 .5 C2.5 3.5 2.5 7.5 5.5 10.5 M5.5 .5 C8.5 3.5 8.5 7.5 5.5 10.5" fill="none" stroke="var(--brand-orange)"/></svg>
    <span>www.brookmereosteopathy.example</span>
  </div>
</section>

</body>
</html>
```